Sunset Harbor Living Web Page

We need a web page design that has two intro pages - first being a 'home page', then a link to the second page that has the 'content tabs' and a 'call to action' (see below).

The business helps people that wish to retire to S.E.Asia (Thailand, Malaysia, Indonesia,The Philippines etc) - to enjoy the lifestyle and the remaining years of their lives. What attracts S.E.Asia to many people is the lower cost, the atmoshpere and beauty of the tropics and the vibrancy of the various countries.

People that are wishing to make the most of their retirement and are adventurous at a great bargain compared to the cost of their own countries will be interested.

We help them achieve this - visa, financials (tax, gov't payments etc), introduce them to the right people for property, clubs, retirement facilities, insurance and so forth.

Therefore we are providing an extremely wide ranging service and this site will provide broad but general information only - with a call to action to come and see us for more specific information and how we can help them specifically.

This site will be predominantly for travel and lifestyle, it will be linked with another financial services (financial planning) site later down the track.

The colour scheme is dark green and blue - as per the attached logo design. Photos and background just think lifestyle and S.E.Asia - beaches/mountains/water/recreational activities for retirees.

Target market is mostly those coming up to retirement to those that are already retired. But we also expect to have some interest with younger people that would like to find out more and plan for the future. So a broad age group but I would say mostly 40-70 yrs old.

On the first (Home) page we would like our company name 'Sunset Harbor Living', our logo (which will be on all pages) and a statement such as: “Imagine a retirement where your dreams are brought to life, and you have never felt more alive. Let us show you how”. Then a link to the second page.

We would like an uncluttered site. On the second (contents) page the tabs would be:

- Visa
- Property
- Financials
- Travel
- Insurance & Healthcare
- Medical Tourism
- Cost of living
- Weekly Blogs and articles
- Sunset Harbor Living story

We would also like a call to action on the second page - asking them to leave their contact details if they wish to learn more or sign up to our weekly newsletter/blog.

We are open to suggestions and your imaginations.

Thank you
Malcolm

Font styles to use
Serif
Script

Colors
0255a3
3377b5
00a990
9bcb3c
abd036
33b8a4
85abd2
cadf82
86cfc6

Requirements
Must have
• I have been asked by the web designer to receive a 'Web Font' so that we can 'get off of Zentrofy'. Hope that makes sense.

```html
<!DOCTYPE html>
<html lang="en">
<head>
<meta charset="utf-8">
<title>Sunset Harbor Living</title>
<link href="https://fonts.googleapis.com/css2?family=Amaranth:wght@400;700&family=Open+Sans:wght@400;600;700&display=swap" rel="stylesheet">
<style>
:root{
  --teal:#00a990;
  --teal-dark:#0a9a82;
  --blue:#0255a3;
  --blue-mid:#3377b5;
  --text:#333;
  --muted:#777;
  --light:#f4f4f4;
  --band:#ececec;
  --footer:#3b3b3b;
  --footer-bottom:#2a2a2a;
  --star:#c9a227;
}
*{box-sizing:border-box;margin:0;padding:0}
html,body{width:1200px;height:2985px;overflow:hidden}
body{font-family:"Open Sans",Arial,sans-serif;color:var(--text);background:#fff;position:relative}
.abs{position:absolute}
.photo{position:absolute;display:block}

/* header */
.header{position:absolute;left:0;top:0;width:1200px;height:150px;background:#fff}
.brand{position:absolute;left:110px;top:46px;display:flex;align-items:center;gap:12px}
.brand-dot{width:40px;height:40px;border-radius:50%;background:var(--teal)}
.brand-name{font-family:"Amaranth",sans-serif;font-weight:700;font-size:30px;color:var(--blue);line-height:1}
.topbar{position:absolute;top:38px;right:95px;display:flex;gap:10px;font-size:12px}
.chip{height:28px;border:1px solid #ddd;border-radius:3px;display:flex;align-items:center;padding:0 10px;gap:6px;color:#444}
.chip.call{border:none}
.chip .ic{width:18px;height:18px;border:1px solid #ccc;border-radius:3px;display:flex;align-items:center;justify-content:center}
.signup{height:28px;background:var(--teal);color:#fff;border-radius:3px;padding:0 12px;display:flex;align-items:center;font-weight:600;font-size:12px}
.nav{position:absolute;top:90px;left:450px;display:flex;gap:44px;font-size:13px;color:#333}
.nav .active{color:var(--teal);position:relative}
.nav .active::after{content:"";position:absolute;left:-4px;top:24px;width:44px;height:4px;border-radius:4px;background:var(--teal)}
.search-ic{position:absolute;left:1088px;top:92px}

/* hero */
.hero{position:absolute;left:0;top:150px;width:1200px;height:478px;background:linear-gradient(90deg,#3f8f9a 0%,#6fb6b8 40%,#c9c0a8 70%,#d8c8a8 100%)}
.hero h1{position:absolute;top:160px;width:100%;text-align:center;font-family:"Amaranth",sans-serif;font-weight:700;font-size:52px;color:#fff}
.hero p{position:absolute;top:238px;left:300px;width:600px;text-align:center;color:#fff;font-size:11.5px;line-height:22px;text-transform:uppercase}
.hero .field{position:absolute;top:310px;width:182px;height:42px;background:#fff;font-size:12px;color:#888;padding:13px 10px}
.hero .go{position:absolute;top:310px;left:838px;width:118px;height:42px;background:var(--teal);color:#fff;font-size:14px;font-weight:600;display:flex;align-items:center;justify-content:center}
.dots{position:absolute;top:418px;left:568px;display:flex;gap:10px}
.dots span{width:16px;height:16px;border-radius:50%;background:rgba(255,255,255,.55)}
.dots span.on{background:#fff}

/* features */
.features{position:absolute;top:628px;left:0;width:1200px;height:68px;background:var(--band)}
.feat{position:absolute;top:14px;display:flex;gap:14px}
.feat .ic{width:28px;height:28px;border-radius:50%;background:#fff;border:1px solid #ccc;display:flex;align-items:center;justify-content:center}
.feat b{display:block;font-weight:400;color:var(--blue-mid);font-size:15px;line-height:20px}
.feat span{font-size:12px;color:#555}

/* section titles */
.sec-title{position:absolute;width:1200px;text-align:center;font-family:"Amaranth",sans-serif;font-weight:700;font-size:30px;color:var(--teal)}
.sec-title .blue{color:var(--blue)}
.rule{position:absolute;left:556px;width:88px;height:2px;background:#d8d8d8}

/* cost of living */
.tile{position:absolute;box-shadow:0 2px 6px rgba(0,0,0,.25)}
.tile .label{position:absolute;left:34px;bottom:30px;color:#fff;font-weight:700;font-size:16px;text-transform:uppercase;line-height:22px}
.tile .label small{display:block;font-weight:400;font-size:13px;text-transform:none}

/* property */
.property-bg{position:absolute;top:1306px;left:0;width:1200px;height:776px;background:var(--light)}
.lead{position:absolute;top:1398px;left:280px;width:640px;text-align:center;font-size:12px;line-height:24px;color:#444}
.card{position:absolute;width:286px;height:272px;background:#fff;box-shadow:0 1px 4px rgba(0,0,0,.12)}
.card .pic{position:absolute;left:0;top:0;width:286px;height:190px}
.card .tag{position:absolute;left:12px;top:18px;background:var(--teal);color:#fff;font-size:11px;padding:6px 12px}
.card .name{position:absolute;left:14px;top:206px;color:var(--blue-mid);font-size:15px;font-weight:600}
.card .heart{position:absolute;right:18px;top:206px}
.card .meta{position:absolute;left:14px;top:236px;font-size:11px;color:#555;display:flex;gap:8px;align-items:center}
.card .stars{color:var(--star);letter-spacing:1px;font-size:12px}
.card .price{position:absolute;right:16px;top:234px;color:var(--blue-mid);font-size:14px}

/* blog */
.post{position:absolute;width:310px}
.post .pic{width:310px;height:172px}
.post h3{margin-top:20px;font-size:15px;font-weight:600;color:#333}
.post .meta{margin-top:8px;display:flex;gap:8px;font-size:10px;color:#666}
.post .meta span{background:#e2e2e2;padding:3px 14px;font-style:italic}
.post .meta .cm{color:var(--blue-mid);font-style:normal}
.post p{margin-top:12px;font-size:12px;line-height:24px;color:#666;text-align:justify}

/* newsletter */
.newsletter{position:absolute;top:2566px;left:0;width:1200px;height:114px;background:var(--teal-dark)}
.newsletter h4{position:absolute;left:242px;top:30px;color:#fff;font-size:19px;font-weight:600}
.newsletter p{position:absolute;left:242px;top:58px;color:#fff;font-size:15px}
.newsletter .email{position:absolute;left:626px;top:30px;width:326px;height:44px;background:#fff;font-size:12px;color:#555;padding:14px 16px}
.newsletter .sub{position:absolute;left:952px;top:30px;width:126px;height:44px;background:#2d2d2d;color:#fff;font-weight:700;font-size:13px;display:flex;align-items:center;justify-content:center}

/* footer */
.footer{position:absolute;top:2680px;left:0;width:1200px;height:256px;background:var(--footer);color:#fff}
.footer h5{position:absolute;top:30px;font-size:14px;font-weight:700;text-transform:uppercase}
.footer h5.story{font-size:18px;text-transform:none;top:26px}
.footer .about{position:absolute;left:100px;top:66px;width:290px;font-size:12px;line-height:26px;text-align:justify}
.footer ul{position:absolute;top:66px;list-style:none;font-size:12px}
.footer li{line-height:26px;display:flex;align-items:center;gap:10px}
.footer li::before{content:"";width:8px;height:8px;border:2px solid #fff;border-radius:50%}
.footer .contact{position:absolute;left:914px;top:66px;font-size:13px;line-height:22px}
.footer .contact .row{display:flex;gap:14px;align-items:center;margin-top:8px}
.bottombar{position:absolute;top:2936px;left:0;width:1200px;height:49px;background:var(--footer-bottom);color:#eee;font-size:11px}
.bottombar .copy{position:absolute;left:100px;top:18px}
.bottombar .links{position:absolute;right:100px;top:18px}
</style>
</head>
<body>

<header class="header">
  <div class="brand"><div class="brand-dot"></div><div class="brand-name">Sunset Harbor Living</div></div>
  <div class="topbar">
    <div class="chip call"><span class="ic"><svg width="10" height="10" viewBox="0 0 24 24"><path d="M6 2l4 4-2 3c1 3 4 6 7 7l3-2 4 4-3 4C10 22 2 14 2 5z" fill="#555"/></svg></span>Call us: +66 20 555 0137</div>
    <div class="chip"><b>$</b> Dollar ▾</div>
    <div class="chip"><svg width="11" height="11" viewBox="0 0 12 12"><circle cx="6" cy="6" r="5.5" fill="var(--blue-mid)"/></svg> English ▾</div>
    <div class="signup">SIGNUP / IN</div>
  </div>
  <nav class="nav">
    <span class="active">Home</span><span>Visa</span><span>Property</span><span>Financials</span><span>Sunset Harbor Living story</span><span>Contact us</span>
  </nav>
  <svg class="search-ic" width="14" height="14" viewBox="0 0 14 14"><circle cx="6" cy="6" r="4.5" fill="none" stroke="var(--teal)" stroke-width="2"/><line x1="9.5" y1="9.5" x2="13" y2="13" stroke="var(--teal)" stroke-width="2"/></svg>
</header>

<section class="hero" role="img" aria-label="Woman in a white sun hat sitting on a tropical beach beside turquoise water">
  <h1>Sunset Harbor Living</h1>
  <p>What attracts S.E.Asia to many people is the lower cost, the atmoshpere and beauty of the tropics and the vibrancy of the various countries.</p>
  <div class="field" style="left:246px">Choose a Destinations</div>
  <div class="field" style="left:444px">Choose a Departure Month</div>
  <div class="field" style="left:642px">Choose a Departure Year</div>
  <div class="go">SEARCH</div>
  <div class="dots"><span></span><span class="on"></span><span></span></div>
</section>

<section class="features">
  <div class="feat" style="left:100px"><div class="ic"><svg width="10" height="14" viewBox="0 0 10 14"><path d="M5 0a5 5 0 0 1 5 5c0 4-5 9-5 9S0 9 0 5a5 5 0 0 1 5-5z" fill="#555"/><circle cx="5" cy="5" r="2" fill="#fff"/></svg></div><div><b>Destinations</b><span>Lorem Ipsum is simply dummy text.</span></div></div>
  <div class="feat" style="left:440px"><div class="ic"><svg width="12" height="12" viewBox="0 0 12 12"><circle cx="6" cy="3.5" r="3" fill="#555"/><path d="M0 12a6 5 0 0 1 12 0z" fill="#555"/></svg></div><div><b>Travel Guides</b><span>Lorem Ipsum is simply dummy text.</span></div></div>
  <div class="feat" style="left:856px"><div class="ic"><svg width="14" height="14" viewBox="0 0 14 14"><circle cx="7" cy="7" r="6" fill="none" stroke="#555" stroke-width="1.5"/><circle cx="5" cy="5.5" r="1" fill="#555"/><circle cx="9" cy="5.5" r="1" fill="#555"/><path d="M4 8.5q3 3 6 0" fill="none" stroke="#555" stroke-width="1.3"/></svg></div><div><b>Happy Customers</b><span>Lorem Ipsum is simply dummy text.</span></div></div>
</section>

<h2 class="sec-title" style="top:736px">Cost of living</h2>
<div class="rule" style="top:792px"></div>

<div class="tile" style="left:156px;top:822px;width:434px;height:436px;background:linear-gradient(180deg,#8fa7c4 0%,#4f7a55 40%,#2f9a94 75%,#6b5a44 100%)" role="img" aria-label="Longtail boat between limestone cliffs in Thailand">
  <div class="label">Thailand<small>Starting from &nbsp;$ 120</small></div></div>
<div class="tile" style="left:612px;top:824px;width:434px;height:154px;background:linear-gradient(180deg,#8aa3b8 0%,#5f8a3c 50%,#3f6e2a 100%)" role="img" aria-label="Green tea plantation hills in Malaysia">
  <div class="label" style="bottom:36px">Malaysia<small>Starting from &nbsp;$ 120</small></div></div>
<div class="tile" style="left:612px;top:1006px;width:206px;height:252px;background:linear-gradient(180deg,#4e7a3a 0%,#6d6a48 60%,#3e4a2c 100%)" role="img" aria-label="Ancient stone temple in the Indonesian jungle">
  <div class="label">Indonesia<small>Starting from &nbsp;$ 320</small></div></div>
<div class="tile" style="left:840px;top:1006px;width:206px;height:252px;background:linear-gradient(180deg,#8fb4d8 0%,#4f7e58 50%,#2ba6b0 100%)" role="img" aria-label="Rocky island lagoon in the Philippines">
  <div class="label">Philippines<small>Starting from &nbsp;$ 320</small></div></div>

<div class="property-bg"></div>
<h2 class="sec-title" style="top:1340px">The Property</h2>
<div class="rule" style="top:1384px"></div>
<p class="lead">Lorem Ipsum is simply dummy text of the printing and typesetting industry. Lorem Ipsum has been the industry's standard dummy text ever since the 1500s.</p>

<div class="card" style="left:140px;top:1462px"><div class="pic photo" style="background:linear-gradient(180deg,#5aa6e0,#2fc0c8 60%,#e8e2c8)" role="img" aria-label="Outrigger boat on a white sand beach"></div><span class="tag">4 Days 3 Nights</span><span class="name">The Philippines</span><svg class="heart" width="16" height="14" viewBox="0 0 16 14"><path d="M8 13S1 8.5 1 4.5A3.5 3.5 0 0 1 8 3a3.5 3.5 0 0 1 7 1.5C15 8.5 8 13 8 13z" fill="none" stroke="var(--teal)" stroke-width="1.5"/></svg><div class="meta"><span class="stars">★★★★☆</span>/ &nbsp;7 Reviews</div><span class="price">$1422</span></div>
<div class="card" style="left:458px;top:1462px"><div class="pic photo" style="background:linear-gradient(180deg,#8ab0d0,#8d6a42 55%,#3f6b3a)" role="img" aria-label="Balinese water temple with mountains behind"></div><span class="tag">4 Days 3 Nights</span><span class="name">Indonesia</span><svg class="heart" width="16" height="14" viewBox="0 0 16 14"><path d="M8 13S1 8.5 1 4.5A3.5 3.5 0 0 1 8 3a3.5 3.5 0 0 1 7 1.5C15 8.5 8 13 8 13z" fill="none" stroke="var(--teal)" stroke-width="1.5"/></svg><div class="meta"><span class="stars">★★★★☆</span>/ &nbsp;7 Reviews</div><span class="price">$1422</span></div>
<div class="card" style="left:776px;top:1462px"><div class="pic photo" style="background:linear-gradient(180deg,#6aa5d8,#3f7a4a 45%,#1fa3a8)" role="img" aria-label="Green tropical islands surrounded by reef"></div><span class="tag">4 Days 3 Nights</span><span class="name">Malaysia</span><svg class="heart" width="16" height="14" viewBox="0 0 16 14"><path d="M8 13S1 8.5 1 4.5A3.5 3.5 0 0 1 8 3a3.5 3.5 0 0 1 7 1.5C15 8.5 8 13 8 13z" fill="none" stroke="var(--teal)" stroke-width="1.5"/></svg><div class="meta"><span class="stars">★★★★☆</span>/ &nbsp;7 Reviews</div><span class="price">$1422</span></div>

<div class="card" style="left:140px;top:1772px"><div class="pic photo" style="background:linear-gradient(180deg,#a7b9c8,#9a7a4e 55%,#5a5030)" role="img" aria-label="Ancient temple ruins with an elephant ride"></div><span class="tag">4 Days 3 Nights</span><span class="name">Thailand</span><svg class="heart" width="16" height="14" viewBox="0 0 16 14"><path d="M8 13S1 8.5 1 4.5A3.5 3.5 0 0 1 8 3a3.5 3.5 0 0 1 7 1.5C15 8.5 8 13 8 13z" fill="none" stroke="var(--teal)" stroke-width="1.5"/></svg><div class="meta"><span class="stars">★★★★☆</span>/ &nbsp;7 Reviews</div><span class="price">$1422</span></div>
<div class="card" style="left:458px;top:1772px"><div class="pic photo" style="background:linear-gradient(180deg,#7cb6e4,#4f7a52 45%,#2bb2b4 70%,#efe6d0)" role="img" aria-label="Longtail boat on a beach below limestone cliffs"></div><span class="tag">4 Days 3 Nights</span><span class="name">The Philippines</span><svg class="heart" width="16" height="14" viewBox="0 0 16 14"><path d="M8 13S1 8.5 1 4.5A3.5 3.5 0 0 1 8 3a3.5 3.5 0 0 1 7 1.5C15 8.5 8 13 8 13z" fill="none" stroke="var(--teal)" stroke-width="1.5"/></svg><div class="meta"><span class="stars">★★★★☆</span>/ &nbsp;7 Reviews</div><span class="price">$1422</span></div>
<div class="card" style="left:776px;top:1772px"><div class="pic photo" style="background:linear-gradient(180deg,#7fa0b8,#5a6a4a 40%,#27c0b4)" role="img" aria-label="Turquoise lagoon enclosed by rocky cliffs"></div><span class="tag">4 Days 3 Nights</span><span class="name">Indonesia</span><svg class="heart" width="16" height="14" viewBox="0 0 16 14"><path d="M8 13S1 8.5 1 4.5A3.5 3.5 0 0 1 8 3a3.5 3.5 0 0 1 7 1.5C15 8.5 8 13 8 13z" fill="none" stroke="var(--teal)" stroke-width="1.5"/></svg><div class="meta"><span class="stars">★★★★☆</span>/ &nbsp;7 Reviews</div><span class="price">$1422</span></div>

<h2 class="sec-title" style="top:2124px">Weekly Blogs <span class="blue">and articles</span></h2>
<div class="rule" style="top:2170px"></div>

<article class="post" style="left:100px;top:2216px"><div class="pic" style="background:linear-gradient(180deg,#7fb2de,#4a7a48 45%,#2cb8b0)" role="img" aria-label="Beach hut and boats in a tropical cove"></div><h3>Finibus Bonorum</h3><div class="meta"><span>September 3, 2015</span><span class="cm">💬 10</span></div><p>Lorem ipsum is simply dummy text of the printing and typesetting industry. Lorem Ipsum has been the industry's standard dummy...</p></article>
<article class="post" style="left:448px;top:2216px"><div class="pic" style="background:linear-gradient(180deg,#6fb0e6,#3fc0c8 45%,#e6dcc4 75%,#7a5a3a)" role="img" aria-label="Palm trees and sun loungers on a white beach"></div><h3>Finibus Bonorum</h3><div class="meta"><span>September 3, 2015</span><span class="cm">💬 10</span></div><p>Lorem ipsum is simply dummy text of the printing and typesetting industry. Lorem Ipsum has been the industry's standard dummy...</p></article>
<article class="post" style="left:796px;top:2216px"><div class="pic" style="background:linear-gradient(180deg,#8ab8e0,#3f6a44 45%,#2a9aa4)" role="img" aria-label="Boat in a bay surrounded by limestone islands"></div><h3>Finibus Bonorum</h3><div class="meta"><span>September 3, 2015</span><span class="cm">💬 10</span></div><p>Lorem ipsum is simply dummy text of the printing and typesetting industry. Lorem Ipsum has been the industry's standard dummy...</p></article>

<section class="newsletter">
  <svg class="abs" style="left:120px;top:14px" width="96" height="86" viewBox="0 0 96 86"><g transform="rotate(-35 48 43)" fill="none" stroke="rgba(255,255,255,.18)" stroke-width="4"><rect x="14" y="20" width="68" height="46"/><path d="M14 20l34 26 34-26"/></g></svg>
  <h4>JOIN OUR NEWSLETTER</h4>
  <p>Lorem ipsum dolor sit amet, consectetur</p>
  <div class="email">Enter your E - mail</div>
  <div class="sub">SUBSCRIBE</div>
</section>

<footer class="footer">
  <h5 class="story" style="left:100px">Sunset Harbor Living story</h5>
  <p class="about">Lorem ipsum dolor sit amet, consectetur adipiscing elit, sed do eiusmod tempor incididunt ut labore et dolore magna aliqua. Ut enim ad minim veniam, quis nostrud exercitation ullamco laboris nisi ut aliquip ex ea commodo consequat.</p>
  <h5 style="left:444px">Quick Link</h5>
  <ul style="left:444px"><li>Thailand</li><li>Malaysia</li><li>Indonesia</li><li>The Philippines</li><li>Visa</li></ul>
  <h5 style="left:650px">Information</h5>
  <ul style="left:650px"><li>Insurance &amp; Healthcare</li><li>Medical Tourism</li><li>Cost of living</li><li>Weekly Blogs and articles</li><li>Visa</li></ul>
  <h5 style="left:914px">Contact Us</h5>
  <div class="contact">
    <div>PO Box 418,<br>Coral Bay NSW 2030</div>
    <div class="row"><svg width="16" height="16" viewBox="0 0 24 24"><path d="M6 2l4 4-2 3c1 3 4 6 7 7l3-2 4 4-3 4C10 22 2 14 2 5z" fill="none" stroke="#fff" stroke-width="1.8"/></svg>+1 0400 555 208</div>
    <div class="row"><svg width="16" height="12" viewBox="0 0 16 12"><rect x="1" y="1" width="14" height="10" fill="none" stroke="#fff" stroke-width="1.4"/><path d="M1 1l7 6 7-6" fill="none" stroke="#fff" stroke-width="1.4"/></svg>hello@sunsetharborliving.example</div>
  </div>
</footer>
<div class="bottombar">
  <span class="copy">Copyright © 2016 Sunset Harbor Living. All Rights Reserved.</span>
  <span class="links">Terms &amp; Conditions &nbsp;/&nbsp; Privacy &amp; Disclaimer &nbsp;/&nbsp; Returns &amp; Refunds</span>
</div>

</body>
</html>
```